Marwick Family Chiropractic Stationary

The letterhead and business card must have our logo.
We would like to see the logo used in different ways ( It can be expanded upon in the stationary.)
Please use the the same or similar colors.
Must be eye catching and memorable.
Must be easy to read

Reason: The doctor has been too busy to make any final decisions. He would like to give himself a little more time.

Target Market(s)

Chiropractic Healthcare

Industry/Entity Type

Business

Requirements
Must have
• Dr. Leonard Marwick D.C.
Chiropractor

860-555-0183

417 Birchfield Road, 2nd Floor
Vernon, CT 06091

drmarwick@marwickspine.example
www.marwickspine.example
www.facebook.com/MarwickFamilySpine
Should not have
• should not be difficult to read

```html
<!DOCTYPE html>
<html lang="en">
<head>
<meta charset="utf-8">
<title>Marwick Family Chiropractic – Business Cards</title>
<link rel="stylesheet" href="https://fonts.googleapis.com/css2?family=Montserrat:wght@700&family=Questrial&display=swap">
<style>
  :root {
    --backdrop: #6e3a22;
    --card-black: #030303;
    --leaf-green: #9cc95a;
    --taupe: #7e7366;
    --warm-grey: #8f877c;
    --white: #ffffff;
    --pattern-dark: #1c1e12;
    --pattern-olive: #3a3d22;
    --social-blue: #3b5ea8;
  }
  * { box-sizing: border-box; margin: 0; padding: 0; }
  html, body {
    width: 1200px; height: 716px; overflow: hidden;
    background: var(--backdrop);
    font-family: "Questrial", "Helvetica Neue", Arial, sans-serif;
  }
  .canvas { position: relative; width: 1200px; height: 716px; }
  .card {
    position: absolute; width: 544px; height: 309px;
    border-radius: 24px; overflow: hidden;
    background: var(--card-black); color: var(--white);
  }
  .card--front { left: 43px; top: 36px; }
  .card--mark { left: 618px; top: 36px; }
  .card--pattern { left: 43px; top: 371px; }
  .card--taupe { left: 618px; top: 367px; background: var(--taupe); }

  /* brand lockup stand-in */
  .brand { position: absolute; text-align: center; font-family: "Montserrat", Arial, sans-serif; font-weight: 700; text-transform: uppercase; white-space: nowrap; }
  .brand__dot { display: block; margin: 0 auto 12px; border-radius: 50%; background: var(--leaf-green); }
  .brand__name { display: block; color: var(--leaf-green); line-height: 1.05; }
  .brand__sub { display: block; color: var(--warm-grey); line-height: 1.2; }

  .card--front .brand { left: 27px; top: 52px; width: 240px; }
  .card--front .brand__dot { width: 96px; height: 96px; }
  .card--front .brand__name { font-size: 32px; }
  .card--front .brand__sub { font-size: 14px; }

  .card--mark .brand, .card--taupe .brand { left: 122px; top: 36px; width: 300px; }
  .card--mark .brand__dot, .card--taupe .brand__dot { width: 140px; height: 140px; }
  .card--mark .brand__name, .card--taupe .brand__name { font-size: 26px; }
  .card--mark .brand__sub, .card--taupe .brand__sub { font-size: 14px; }
  .card--taupe .brand__dot { background: var(--white); }
  .card--taupe .brand__name, .card--taupe .brand__sub { color: var(--white); }

  /* contact column */
  .contact__accent { position: absolute; left: 532px; top: 14px; width: 12px; height: 228px; background: var(--leaf-green); }
  .contact { position: absolute; right: 44px; top: 0; text-align: right; }
  .contact__name { position: absolute; right: 0; top: 40px; white-space: nowrap; font-size: 15px; font-weight: 700; color: var(--leaf-green); letter-spacing: -0.2px; }
  .contact__role { position: absolute; right: 0; top: 61px; white-space: nowrap; font-size: 14px; color: var(--warm-grey); }
  .contact__lines { position: absolute; right: 0; white-space: nowrap; font-size: 14px; }
  .contact__lines--address { top: 105px; line-height: 21px; }
  .contact__lines--reach { top: 172px; line-height: 23px; }
  .icon { display: inline-block; width: 10px; height: 10px; margin-right: 5px; vertical-align: -1px; }
  .icon--square { background: var(--social-blue); border-radius: 1px; }

  .web { position: absolute; left: 0; width: 100%; text-align: center; font-size: 14px; letter-spacing: 2px; color: var(--white); white-space: nowrap; }
  .card--front .web { width: auto; left: auto; right: 44px; top: 260px; text-align: right; }
  .web__accent { color: var(--leaf-green); }
  .card--mark .web { top: 262px; }
  .card--taupe .web { top: 258px; }

  .pattern-field { position: absolute; inset: 0; background: radial-gradient(circle at 50% 50%, var(--pattern-olive), var(--pattern-dark) 75%); }
  .pattern-title { position: absolute; left: 0; width: 100%; top: 86px; text-align: center; font-family: "Montserrat", Arial, sans-serif; font-weight: 700; text-transform: uppercase; line-height: 1.1; white-space: nowrap; }
  .pattern-title__main { display: block; font-size: 60px; letter-spacing: 1px; color: var(--leaf-green); }
  .pattern-title__sub { display: block; font-size: 26px; letter-spacing: 1px; color: var(--warm-grey); }
  .card--pattern .web { top: 252px; }
</style>
</head>
<body>
<main class="canvas">

  <section class="card card--front" aria-label="Business card front">
    <div class="brand">
      <span class="brand__dot"></span>
      <span class="brand__name">Marwick</span>
      <span class="brand__sub">Family Chiropractic</span>
    </div>
    <div class="contact__accent"></div>
    <div class="contact">
      <p class="contact__name">Dr. Leonard Marwick D.C.</p>
      <p class="contact__role">Chiropractor</p>
      <p class="contact__lines contact__lines--address">417 Birchfield Road<br>Suite 2B, Ellsworth Falls, CT 06091</p>
      <p class="contact__lines contact__lines--reach">
        <svg class="icon" viewBox="0 0 10 10" aria-hidden="true"><circle cx="5" cy="5" r="4.3" fill="none" stroke="#9cc95a" stroke-width="1.2"/><path d="M3.4 2.8 L4.4 4.2 L3.9 4.9 Q4.6 6.2 5.6 6.4 L6.2 5.9 L7.4 6.8" fill="none" stroke="#9cc95a" stroke-width="1"/></svg>860-555-0183<br>
        <svg class="icon" viewBox="0 0 10 10" aria-hidden="true"><rect x="0.5" y="2" width="9" height="6.5" fill="#9cc95a"/><path d="M0.5 2 L5 6 L9.5 2" fill="none" stroke="#030303" stroke-width="0.9"/></svg>mymarwick@marwickspine.example<br>
        <span class="icon icon--square"></span>MarwickFamilySpine
      </p>
    </div>
    <p class="web">www.<span class="web__accent">marwickspine</span>.example</p>
  </section>

  <section class="card card--mark" aria-label="Business card back, brand mark">
    <div class="brand">
      <span class="brand__dot"></span>
      <span class="brand__name">Marwick</span>
      <span class="brand__sub">Family Chiropractic</span>
    </div>
    <p class="web">www.marwickspine.example</p>
  </section>

  <section class="card card--pattern" aria-label="Business card back, patterned">
    <div class="pattern-field" role="img" aria-label="Repeating pattern of small dark leafy tree emblems"></div>
    <h2 class="pattern-title">
      <span class="pattern-title__main">Marwick</span>
      <span class="pattern-title__sub">Family Chiropractic</span>
    </h2>
    <p class="web">www.marwickspine.example</p>
  </section>

  <section class="card card--taupe" aria-label="Business card back, taupe">
    <div class="brand">
      <span class="brand__dot"></span>
      <span class="brand__name">Marwick</span>
      <span class="brand__sub">Family Chiropractic</span>
    </div>
    <p class="web">www.marwickspine.example</p>
  </section>

</main>
</body>
</html>
```